Card Design for my dog training business Brightpaw Obedience

Need a business card design for my dog training business with my new logo. Want the card to come off professional yet fun. Want it to be very eye catchy as well. I normally have these at vet clinics, pet stores, and groomers. so need it to look better than my competitors.
Target Market(s)
dog owners
Industry/Entity Type
Dog Training
Contact Information for Business Card
needs logo, my name and info
Font styles to use
Serif
Colors
0255a3
ffffff
ec1f27
000000
333333
fbfbfb
Requirements
Must have
- Brightpaw Obedience
- Felix Orland
- 415 903 2276
- info@brightpawobedience.example
- www.brightpawobedience.example

```html
<!DOCTYPE html>
<html lang="en">
<head>
<meta charset="utf-8">
<title>Brightpaw Obedience – Business Card</title>
<link rel="stylesheet" href="https://fonts.googleapis.com/css2?family=Cinzel:wght@400&family=Crimson+Text:ital,wght@0,400;1,400&display=swap">
<style>
  :root {
    --page-bg: #e9e6e1;
    --card-white: #ffffff;
    --pattern-light: #f4f4f4;
    --pattern-mid: #e2e2e2;
    --pattern-deep: #d6d6d6;
    --brand-red: #ec1f27;
    --ink: #000000;
    --ink-soft: #333333;
    --card-black: #0b0b0b;
    --silver: #c4c4c4;
    --silver-dim: #9a9a9a;
  }
  * { box-sizing: border-box; margin: 0; padding: 0; }
  html, body {
    width: 900px; height: 1200px; overflow: hidden;
    background: var(--page-bg);
  }
  .canvas { position: relative; width: 900px; height: 1200px; }

  .card {
    position: absolute; left: 82px; width: 734px;
    border-radius: 22px; overflow: hidden;
    box-shadow: 0 6px 18px rgba(0,0,0,.18);
  }

  /* Front */
  .card--front { top: 138px; height: 427px; background: var(--card-white); }
  .pet-pattern {
    position: absolute; inset: 0 0 35px 0;
    background:
      radial-gradient(ellipse at 20% 15%, var(--card-white) 0%, transparent 45%),
      radial-gradient(ellipse at 85% 80%, var(--pattern-deep) 0%, transparent 55%),
      linear-gradient(135deg, var(--pattern-light) 0%, var(--pattern-mid) 60%, var(--pattern-deep) 100%);
  }
  .logo-art {
    position: absolute; left: 68px; top: 57px; width: 277px; height: 190px;
    background: linear-gradient(160deg, #2a2a2a, #5a5a5a);
    border-radius: 4px;
  }
  .logo-name {
    position: absolute; left: 40px; width: 345px; top: 256px;
    text-align: center; font-family: "Cinzel", serif; font-weight: 400;
    color: var(--ink); font-size: 30px; line-height: 36px;
  }
  .divider {
    position: absolute; left: 373px; top: 62px; width: 1px; height: 258px;
    background: var(--ink-soft);
  }
  .person-name {
    position: absolute; left: 406px; top: 112px;
    font-family: "Cinzel", serif; font-weight: 400; font-size: 25px; letter-spacing: .5px;
    color: var(--ink); text-transform: uppercase;
  }
  .contact-list { position: absolute; left: 406px; top: 159px; list-style: none; }
  .contact-item {
    display: flex; align-items: center; height: 34px; margin-bottom: 6px;
    font-family: "Crimson Text", serif; font-size: 18px; color: var(--ink);
  }
  .contact-icon { width: 34px; height: 34px; margin-right: 13px; flex: none; }
  .service-band {
    position: absolute; left: 0; right: 0; bottom: 0; height: 35px;
    background: var(--brand-red); color: var(--card-white);
    display: flex; align-items: center; justify-content: center; gap: 8px;
    font-family: "Crimson Text", serif; font-size: 17px; letter-spacing: .5px;
    text-transform: uppercase;
  }
  .service-dot { width: 9px; height: 9px; border-radius: 50%; background: var(--card-white); }

  /* Back */
  .card--back {
    top: 633px; height: 429px;
    background: radial-gradient(ellipse at 50% 30%, #1b1b1b 0%, var(--card-black) 70%);
  }
  .logo-art--back {
    position: absolute; left: 213px; top: 45px; width: 300px; height: 200px;
    background: linear-gradient(160deg, #8a8a8a, #3e3e3e);
    border-radius: 4px;
  }
  .logo-name--back {
    position: absolute; left: 0; right: 0; top: 254px; text-align: center;
    font-family: "Cinzel", serif; font-weight: 400; color: var(--silver);
    font-size: 32px; line-height: 40px;
  }
  .tagline {
    position: absolute; left: 0; right: 0; top: 362px; text-align: center;
    font-family: "Crimson Text", serif; font-style: italic; font-size: 15px;
    color: var(--silver-dim);
  }
</style>
</head>
<body>
<main class="canvas">

  <section class="card card--front" aria-label="Business card front">
    <div class="pet-pattern" role="img" aria-label="Playful light grey pattern of pet icons: dogs, bones, paw prints, kennels, collars, food bowls and grooming tools"></div>
    <div class="logo-art" role="img" aria-label="Logo illustration: outline of a state map with two dog heads"></div>
    <div class="logo-name">Brightpaw<br>Obedience</div>
    <div class="divider"></div>
    <h1 class="person-name">Felix Orland</h1>
    <ul class="contact-list">
      <li class="contact-item">
        <svg class="contact-icon" viewBox="0 0 34 34" aria-hidden="true">
          <circle cx="17" cy="17" r="15.5" fill="var(--card-white)" stroke="var(--brand-red)" stroke-width="2"/>
          <path d="M12 10c1.5-1 2.5 0 3 1.5l.8 2c.3 1-.5 1.6-1.2 2 .8 1.8 2 3 3.8 3.8.4-.7 1-1.5 2-1.2l2 .8c1.5.5 2.5 1.5 1.5 3-1 1.6-2.5 2.2-4.5 1.5-4-1.5-7-4.5-8.5-8.5-.7-2-.1-3.5 1.1-4.9z" fill="var(--brand-red)"/>
        </svg>
        415 903 2276
      </li>
      <li class="contact-item">
        <svg class="contact-icon" viewBox="0 0 34 34" aria-hidden="true">
          <circle cx="17" cy="17" r="15.5" fill="var(--card-white)" stroke="var(--brand-red)" stroke-width="2"/>
          <rect x="10" y="12" width="14" height="10" fill="var(--brand-red)"/>
          <path d="M10 12l7 6 7-6" fill="none" stroke="var(--card-white)" stroke-width="1.4"/>
        </svg>
        info@brightpawobedience.example
      </li>
      <li class="contact-item">
        <svg class="contact-icon" viewBox="0 0 34 34" aria-hidden="true">
          <circle cx="17" cy="17" r="15.5" fill="var(--card-white)" stroke="var(--brand-red)" stroke-width="2"/>
          <g fill="none" stroke="var(--brand-red)" stroke-width="1.4">
            <circle cx="17" cy="17" r="8"/>
            <ellipse cx="17" cy="17" rx="3.5" ry="8"/>
            <path d="M9 17h16M10.5 13h13M10.5 21h13"/>
          </g>
        </svg>
        www.brightpawobedience.example
      </li>
    </ul>
    <div class="service-band">
      <span class="service-dot"></span>Vet Clinics
      <span class="service-dot"></span>Pet Stores
      <span class="service-dot"></span>Groomers.
    </div>
  </section>

  <section class="card card--back" aria-label="Business card back">
    <div class="logo-art--back" role="img" aria-label="Logo illustration in silver: outline of a state map with two dog heads"></div>
    <div class="logo-name--back">Brightpaw<br>Obedience</div>
    <p class="tagline">“Training dogs across the bay one dog at a time.”</p>
  </section>

</main>
</body>
</html>
```